Product Label with Company Logo & Product Information

I am looking for a new label design for one of my products, Candied Pecans. I am including an old label that I made, but it does not "pop" on the current packaging. See image of current packaging attached as well.

I want the design to ultimately be something that I can take and order a roll of labels/stickers. Please stick within standard label/sticker sizes (round or square). Please include final size as well.

Must Haves:
(1) Company logo (any color variation-see attached logo images).
(2) All wording on the old label
(3) Label size can not be more than 2 in. x 4 in. (I would actually like them a little smaller). They seem kind of big as they are right now.

```html
<!DOCTYPE html>
<html lang="en">
<head>
<meta charset="utf-8">
<title>Meadow Hive – Gourmet Candied Pecans Label</title>
<link rel="stylesheet" href="https://fonts.googleapis.com/css2?family=Grenze+Gotisch:wght@500;600&family=Playfair+Display:wght@900&family=Roboto:wght@700&display=swap">
<style>
  :root {
    --backdrop: #232323;
    --label-ink: #202024;
    --honey: #f2ec2c;
    --slate: #5b5b5f;
    --slate-soft: #4a4a4e;
    --bee-black: #111113;
  }
  * { margin: 0; padding: 0; box-sizing: border-box; }
  html, body {
    width: 1200px; height: 780px; overflow: hidden;
    background: var(--backdrop);
  }
  .label {
    position: absolute; left: 73px; top: 134px;
    width: 1012px; height: 506px;
    background: var(--label-ink);
    overflow: hidden;
  }
  .label__wave { position: absolute; inset: 0; }
  .brand {
    position: absolute; left: 40px; top: 96px;
    display: flex; align-items: center; gap: 14px;
    white-space: nowrap;
  }
  .brand__mark {
    width: 34px; height: 34px; background: var(--honey);
  }
  .brand__name {
    font-family: "Grenze Gotisch", serif; font-weight: 600;
    font-size: 62px; line-height: 1; color: var(--honey);
  }
  .title {
    position: absolute; right: 36px; top: 14px; text-align: right;
    white-space: nowrap;
  }
  .title__kicker {
    font-family: "Playfair Display", serif; font-weight: 900;
    font-size: 64px; line-height: 1; letter-spacing: -1px;
    color: var(--slate);
  }
  .title__product {
    margin-top: 8px;
    font-family: "Playfair Display", serif; font-weight: 900;
    font-size: 43px; line-height: 1; letter-spacing: 1px;
    color: var(--honey);
  }
  .ingredients {
    position: absolute; left: 24px; top: 292px;
    font-family: "Grenze Gotisch", serif; font-weight: 500;
    font-size: 36px; line-height: 41px; color: var(--honey);
    white-space: nowrap;
  }
  .bee-art {
    position: absolute; left: 668px; top: 150px;
    width: 284px; height: 232px;
  }
  .contact {
    position: absolute; left: 658px; top: 388px;
    color: var(--slate);
    white-space: nowrap;
  }
  .contact__phone {
    display: flex; align-items: center; gap: 16px;
    font-family: "Roboto", sans-serif; font-weight: 700;
    font-size: 40px; line-height: 1;
  }
  .contact__company {
    margin-top: 12px;
    font-family: "Grenze Gotisch", serif; font-weight: 600;
    font-size: 32px; line-height: 1; color: var(--slate-soft);
  }
</style>
</head>
<body>
  <section class="label" aria-label="Gourmet Candied Pecans product label">
    <svg class="label__wave" viewBox="0 0 1012 506" preserveAspectRatio="none" aria-hidden="true">
      <defs>
        <linearGradient id="honeyFade" x1="0" y1="0" x2="1" y2="0">
          <stop offset="0" stop-color="#2a2a28"/>
          <stop offset="0.45" stop-color="#7a7540"/>
          <stop offset="0.7" stop-color="#c9c23a"/>
          <stop offset="0.85" stop-color="#f2ec2c"/>
        </linearGradient>
        <linearGradient id="swooshFade" x1="0" y1="0" x2="1" y2="0">
          <stop offset="0" stop-color="#f2ec2c"/>
          <stop offset="0.55" stop-color="#f2ec2c" stop-opacity="0.35"/>
          <stop offset="1" stop-color="#f2ec2c" stop-opacity="0"/>
        </linearGradient>
      </defs>
      <path d="M0,420 C170,510 430,520 620,440 C760,380 820,320 900,292 C950,276 990,290 1012,305 L1012,506 L0,506 Z" fill="url(#honeyFade)"/>
      <path d="M0,363 C110,440 250,480 380,478 C300,486 150,460 0,410 Z" fill="url(#swooshFade)"/>
      <path d="M0,410 C150,470 320,495 460,478 C330,500 160,490 0,440 Z" fill="var(--label-ink)" opacity="0.7"/>
    </svg>

    <div class="brand">
      <span class="brand__mark"></span>
      <span class="brand__name">Meadow Hive</span>
    </div>

    <div class="title">
      <p class="title__kicker">GOURMET</p>
      <p class="title__product">CANDIED PECANS</p>
    </div>

    <p class="ingredients">Made with Cinnamon<br>Brown Sugar &amp; Salt Order More</p>

    <svg class="bee-art" viewBox="0 0 284 232" role="img" aria-label="Illustration of a large black stylised bee with curled wings">
      <defs>
        <radialGradient id="beeTone" cx="0.5" cy="0.45" r="0.6">
          <stop offset="0" stop-color="#2a2a2d"/>
          <stop offset="1" stop-color="#111113"/>
        </radialGradient>
      </defs>
      <rect x="10" y="8" width="264" height="216" rx="90" fill="url(#beeTone)"/>
    </svg>

    <div class="contact">
      <p class="contact__phone">
        <svg width="42" height="46" viewBox="0 0 42 46" aria-hidden="true">
          <path d="M21 1 L40 12 L40 34 L21 45 L2 34 L2 12 Z" fill="var(--slate)"/>
          <path d="M14 13 c-2 1 -3 3 -2 6 c2 7 7 12 14 14 c3 1 5 0 6-2 l-4-4 c-1 0-2 1-3 1 c-3-1-6-4-7-7 c0-1 1-2 1-3 Z" fill="var(--honey)"/>
        </svg>
        <span>(555)014-2231</span>
      </p>
      <p class="contact__company">Meadow Hive Market, LLC</p>
    </div>
  </section>
</body>
</html>
```